Communication and Marketing agency needs a new presentation card

We are a group of communication and marketing agencies specialized in companies that are in the logistics and industrial sector. The head agency is TELVANO Grupo and the group consists of 4 agencies: TELVANO Media, TELVANO Digital, TELVANO Research and DifundeEnPantalla. We hace 4 offices in Spain (Madrid, Barcelona, Valencia and Murcia). We are looking for a clean and attractive design that transmits our experience, brand presence in the market and knowledge to those who receive the card.It has to maintain the colors of the logo that is attached.
Target Market(s)
logistics and industrial sector
Marketing department
Contact Information for Business Card
Clean and attractive design

```html
<!DOCTYPE html>
<html lang="en">
<head>
<meta charset="utf-8">
<title>TELVANO Grupo — Business Card</title>
<link href="https://fonts.googleapis.com/css2?family=Open+Sans:wght@400;600&display=swap" rel="stylesheet">
<style>
  :root {
    --backdrop: #77787d;
    --card-light: #ececec;
    --card-dark: #2b2b2c;
    --brand-red: #a31c22;
    --ink: #3d3d3d;
    --ink-light: #d8d8d8;
  }
  * { margin: 0; padding: 0; box-sizing: border-box; }
  html, body { width: 1200px; height: 1144px; overflow: hidden; }
  body {
    background: var(--backdrop);
    font-family: "Open Sans", Arial, sans-serif;
    position: relative;
  }
  .card {
    position: absolute;
    left: 255px;
    width: 691px;
    height: 394px;
  }
  .card--front {
    top: 150px;
    background: linear-gradient(135deg, #f2f2f2 0%, var(--card-light) 55%, #dedede 100%);
  }
  .card--back {
    top: 602px;
    background: var(--card-dark);
  }

  /* Front: brand */
  .front-brand {
    position: absolute;
    left: 67px;
    top: 152px;
    width: 253px;
    text-align: right;
    color: var(--brand-red);
    font-weight: 600;
  }
  .front-brand .brand-name { display: block; font-size: 46px; line-height: 46px; letter-spacing: 2px; }
  .front-brand .brand-sub { display: block; font-size: 30px; line-height: 34px; }

  /* Front: contact block */
  .contact {
    position: absolute;
    left: 382px;
    top: 90px;
    width: 237px;
    color: var(--ink);
  }
  .contact__name {
    font-weight: 600;
    font-size: 27px;
    line-height: 32px;
    color: var(--brand-red);
    letter-spacing: -0.3px;
    white-space: nowrap;
  }
  .contact__role {
    font-size: 18px;
    line-height: 22px;
    padding-bottom: 6px;
    border-bottom: 2px solid var(--brand-red);
  }
  .contact__address {
    margin-top: 20px;
    font-size: 15.5px;
    line-height: 22px;
  }
  .contact__list {
    list-style: none;
    margin-top: 18px;
    font-size: 15.5px;
    line-height: 20.5px;
  }
  .contact__list li { display: flex; align-items: center; gap: 7px; white-space: nowrap; }
  .contact__list svg { width: 13px; height: 13px; flex: none; fill: var(--brand-red); }

  /* Back */
  .back-brand {
    position: absolute;
    left: 168px;
    top: 130px;
    width: 357px;
    text-align: right;
    color: var(--brand-red);
    font-weight: 600;
  }
  .back-brand .brand-name { display: block; font-size: 66px; line-height: 66px; letter-spacing: 3px; }
  .back-brand .brand-sub { display: block; font-size: 42px; line-height: 48px; }

  .agencies {
    position: absolute;
    left: 180px;
    top: 318px;
    display: flex;
    gap: 14px;
  }
  .agency {
    width: 104px;
    text-align: right;
    color: var(--ink-light);
    font-weight: 600;
  }
  .agency .brand-name { display: block; font-size: 17px; line-height: 18px; letter-spacing: 0.5px; }
  .agency .brand-sub { display: block; font-size: 11px; line-height: 13px; }
</style>
</head>
<body>

  <section class="card card--front" aria-label="Card front">
    <div class="front-brand">
      <span class="brand-name">TELVANO</span>
      <span class="brand-sub">Grupo</span>
    </div>

    <div class="contact">
      <p class="contact__name">MARTA QUILES</p>
      <p class="contact__role">Founder</p>
      <p class="contact__address">48 Calle Alcalde Roca<br>30001 Murcia, Spain</p>
      <ul class="contact__list">
        <li>
          <svg viewBox="0 0 24 24" aria-hidden="true"><path d="M6.6 10.8a15 15 0 0 0 6.6 6.6l2.2-2.2c.3-.3.7-.4 1-.2 1.1.4 2.3.6 3.6.6.6 0 1 .4 1 1V20c0 .6-.4 1-1 1A17 17 0 0 1 3 4c0-.6.4-1 1-1h3.5c.6 0 1 .4 1 1 0 1.3.2 2.5.6 3.6.1.3 0 .7-.2 1z"/></svg>
          (000) 555-018-42
        </li>
        <li>
          <svg viewBox="0 0 24 24" aria-hidden="true"><path d="M2 5h20v14H2z M2 5l10 7 10-7" fill="var(--brand-red)"/><path d="M3 6l9 6.3L21 6" fill="none" stroke="#ececec" stroke-width="1.6"/></svg>
          hola@telvanogrupo.com
        </li>
        <li>
          <svg viewBox="0 0 24 24" aria-hidden="true"><circle cx="12" cy="12" r="10"/><path d="M2 12h20M12 2c3 3 3 17 0 20M12 2c-3 3-3 17 0 20" fill="none" stroke="#ececec" stroke-width="1.4"/></svg>
          www.telvanogrupo.com
        </li>
      </ul>
    </div>
  </section>

  <section class="card card--back" aria-label="Card back">
    <div class="back-brand">
      <span class="brand-name">TELVANO</span>
      <span class="brand-sub">Grupo</span>
    </div>

    <div class="agencies">
      <div class="agency">
        <span class="brand-name">TELVANO</span>
        <span class="brand-sub">Research</span>
      </div>
      <div class="agency">
        <span class="brand-name">TELVANO</span>
        <span class="brand-sub">Media</span>
      </div>
      <div class="agency">
        <span class="brand-name">TELVANO</span>
        <span class="brand-sub">Digital</span>
      </div>
    </div>
  </section>

</body>
</html>
```